stationary deign for trucking company

im a trucking company looking for a professional set of stationary designs i deliver goods from point a to b
Updates

When submitting stationary designs I need envelope design, letterhead, cards, I’d badge etc

Industry/Entity Type

Trucking Company

Requirements
Must have
• must have letter head, business card, envelope, fax sheet, id badge, folder, thank you card, notebook, invoice sheet.
Nice to have
• nice to have them all custom made (letterhead,envelope, business card, I’d badge etc
Should not have
• must not have prepaid sign want i unique design for items

```html
<!DOCTYPE html>
<html lang="en">
<head>
<meta charset="utf-8">
<title>Marlow Freight – Business Card</title>
<link href="https://fonts.googleapis.com/css2?family=Arimo:wght@400;700&display=swap" rel="stylesheet">
<style>
  :root {
    --backdrop: #1e1e1e;
    --card: #f1f1f1;
    --ink: #111111;
    --muted: #5a5a5a;
    --brand-blue: #1a5aa8;
    --line: #222222;
  }
  html, body {
    margin: 0;
    padding: 0;
    overflow: hidden;
  }
  .canvas {
    position: relative;
    width: 1200px;
    height: 800px;
    background: var(--backdrop);
    overflow: hidden;
    font-family: "Arimo", Arial, sans-serif;
  }
  .card {
    position: absolute;
    width: 312px;
    height: 528px;
    background: var(--card);
  }
  .card--front { left: 260px; top: 111px; }
  .card--back  { left: 630px; top: 115px; }

  .brand {
    position: absolute;
    left: 0;
    right: 0;
    top: 256px;
    display: flex;
    align-items: center;
    justify-content: center;
    gap: 12px;
  }
  .brand__mark {
    width: 24px;
    height: 24px;
    border: 2px solid var(--ink);
    box-sizing: border-box;
    flex: none;
  }
  .brand__name {
    font-size: 19px;
    font-weight: 400;
    letter-spacing: 2px;
    line-height: 24px;
    color: var(--ink);
    white-space: nowrap;
  }

  .contact {
    position: absolute;
    inset: 0;
    text-align: center;
  }
  .contact__name {
    position: absolute;
    left: 0; right: 0;
    top: 145px;
    margin: 0;
    font-size: 25px;
    font-weight: 700;
    color: var(--brand-blue);
  }
  .contact__title {
    position: absolute;
    left: 0; right: 0;
    top: 173px;
    margin: 0;
    font-size: 17px;
    color: var(--ink);
  }
  .divider {
    position: absolute;
    left: 0; right: 0;
    top: 210px;
    display: flex;
    align-items: center;
    justify-content: center;
    gap: 2px;
  }
  .divider__rule {
    width: 42px;
    height: 1px;
    background: var(--line);
  }
  .divider__rule--left { margin-right: 4px; }
  .divider__rule--right { margin-left: 4px; }
  .contact__block {
    position: absolute;
    left: 0; right: 0;
    margin: 0;
    font-size: 15.5px;
    line-height: 20px;
    color: var(--muted);
  }
  .contact__address { top: 251px; }
  .contact__lines { top: 305px; }
  .contact__web {
    position: absolute;
    left: 0; right: 0;
    top: 386px;
    margin: 0;
    font-size: 16px;
    color: var(--ink);
  }
  .contact__web span { color: var(--brand-blue); }
</style>
</head>
<body>
<main class="canvas">
  <section class="card card--front" aria-label="Card front">
    <div class="brand">
      <span class="brand__mark"></span>
      <span class="brand__name">MARLOW FREIGHT</span>
    </div>
  </section>

  <section class="card card--back" aria-label="Card back">
    <div class="contact">
      <h1 class="contact__name">DANIEL REYES</h1>
      <p class="contact__title">CEO/Founder</p>

      <div class="divider">
        <span class="divider__rule divider__rule--left"></span>
        <svg width="26" height="26" viewBox="0 0 26 26" aria-label="Phone">
          <rect x="5" y="5" width="16" height="16" transform="rotate(45 13 13)" fill="none" stroke="#111" stroke-width="1.8"/>
          <path d="M10 9.5 l1.5 -0.5 l1.2 2.2 l-1 0.8 q0.8 1.8 2.3 2.6 l0.8 -1 l2.2 1.2 l-0.5 1.5 q-4.5 0 -6.5 -6.8z" fill="#1a5aa8"/>
        </svg>
        <svg width="26" height="26" viewBox="0 0 26 26" aria-label="Mobile">
          <rect x="5" y="5" width="16" height="16" transform="rotate(45 13 13)" fill="none" stroke="#111" stroke-width="1.8"/>
          <rect x="10.7" y="8.5" width="4.6" height="9" rx="0.8" fill="none" stroke="#1a5aa8" stroke-width="1.2"/>
          <circle cx="13" cy="16" r="0.6" fill="#1a5aa8"/>
        </svg>
        <svg width="26" height="26" viewBox="0 0 26 26" aria-label="Email">
          <rect x="5" y="5" width="16" height="16" transform="rotate(45 13 13)" fill="none" stroke="#111" stroke-width="1.8"/>
          <rect x="9.2" y="10.3" width="7.6" height="5.4" fill="#1a5aa8"/>
          <path d="M9.2 10.3 L13 13.3 L16.8 10.3" fill="none" stroke="#f1f1f1" stroke-width="0.8"/>
        </svg>
        <span class="divider__rule divider__rule--right"></span>
      </div>

      <p class="contact__block contact__address">4120 Birchwood Avenue<br>Fairbanks, Alaska 99701</p>
      <p class="contact__block contact__lines">555-214-7038<br>555-386-4190<br>daniel@marlowfreight.com</p>
      <p class="contact__web">www.<span>marlowfreight</span>.com</p>
    </div>
  </section>
</main>
</body>
</html>
```